zorvan lumet website design

An IT support and IT Security Company - just use dummy text for now for the design. Examples of sites we like the looks and feel of but need it more professional feel are like: www.kelbrovault.uk.com , www.pravok.co.uk, www.quenthardy.com/professional/, www.vur.com, www.melvish.com,

Best to message me if you have any questions

Target Market(s)

small to medium UK based companies that require IT support services

Industry/Entity Type

It Company

Contact Information for Business Card

use dummy name, telephone and email for now, will provide details later.

Logo Text

zorvan lumet (and then below the logo it should say "your IT, networks and security partner")

Coding

Coded - Design and coding required

Number of Pages Required

5+ page

Colors

Designer to choose colors to be used in the design.

Requirements
Must have
• must be professional, yet simple and clear that this is a serious IT support and IT security company.
Nice to have
• 1)The website homepage must have professional quality pictures of IT support or London city skyline or any picture that projects friendly business partners, professionalism and ready to serve.
• 2) Home page needs to include tabs for following pages 'Services' , 'About Us' , 'Contact Us' 'Home'
• 3) Website built customised using wordpress is ideal and easy for us to manage.
• more room for boxed options from homepage (with pic or image in background)
Should not have
• no checkout trolleys or payment options.

```html
<!DOCTYPE html>
<html lang="en">
<head>
<meta charset="utf-8">
<title>Zorvan Lumet</title>
<link href="https://fonts.googleapis.com/css2?family=Open+Sans:wght@400;600;700&family=Ubuntu:wght@400;500;700&display=swap" rel="stylesheet">
<style>
:root{
  --orange:#f0673f;
  --teal:#36b3bd;
  --amber:#f6a21b;
  --purple:#7a3994;
  --ink:#2d2d2d;
  --body:#7a7a7a;
  --line:#e4e4e4;
  --footer:#1f1f1f;
  --white:#ffffff;
}
*{margin:0;padding:0;box-sizing:border-box}
html,body{width:1200px;height:2748px;overflow:hidden;background:var(--white)}
body{font-family:"Open Sans",Arial,sans-serif;color:var(--body);position:relative}
h1,h2,h3,h4{font-family:"Ubuntu",Arial,sans-serif;font-weight:500;color:var(--ink)}

/* header */
.site-header{position:absolute;left:0;top:0;width:1200px;height:100px;border-top:5px solid var(--orange);background:var(--white)}
.brand{position:absolute;left:99px;top:20px;display:flex;align-items:center;gap:12px}
.brand-dot{width:44px;height:44px;border-radius:50%;background:var(--purple);flex:none}
.brand-text{display:flex;flex-direction:column}
.brand-name{font-family:"Ubuntu",sans-serif;font-weight:500;font-size:32px;line-height:36px;color:var(--ink)}
.brand-tagline{font-family:"Ubuntu",sans-serif;font-weight:500;font-size:10.5px;line-height:14px;color:var(--ink);letter-spacing:.2px}
.main-nav{position:absolute;left:418px;top:0;height:95px;display:flex;align-items:stretch}
.main-nav a{display:flex;align-items:center;gap:8px;padding:0 25px;font-size:14px;color:var(--ink);text-decoration:none}
.main-nav a.active{background:var(--orange);color:var(--white);font-weight:600;padding:0 22px}
.main-nav svg{width:12px;height:12px}
.login-btn{position:absolute;left:927px;top:33px;width:172px;height:38px;background:var(--purple);color:var(--white);border-radius:3px;font-size:13.5px;font-weight:600;display:flex;align-items:center;justify-content:center;gap:8px;letter-spacing:.2px}

/* hero */
.hero{position:absolute;left:0;top:100px;width:1200px;height:486px;overflow:hidden;
  background:
    radial-gradient(ellipse 320px 260px at 380px 250px,rgba(120,96,70,.55),transparent 70%),
    radial-gradient(ellipse 520px 120px at 760px 380px,rgba(70,110,90,.55),transparent 70%),
    linear-gradient(180deg,#6f7594 0%,#a59fb6 22%,#c6b3b8 40%,#9c8570 58%,#5d5a55 74%,#2b2e36 100%)}
.hero-title{position:absolute;right:99px;top:118px;font-family:"Open Sans",sans-serif;font-size:50px;font-weight:600;color:var(--white);letter-spacing:1px}
.hero-sub{position:absolute;right:99px;top:196px;font-size:16px;color:#f2f2f2;display:flex;gap:10px;align-items:center}
.hero-sub i{width:7px;height:7px;border-radius:50%;background:var(--white);display:inline-block}
.hero-dots{position:absolute;left:561px;top:431px;display:flex;gap:10px}
.hero-dots span{width:11px;height:11px;border-radius:50%;border:2px solid var(--white)}
.hero-dots span.on{background:var(--white)}

/* partners */
.partners{position:absolute;left:123px;top:636px;width:956px;display:grid;grid-template-columns:repeat(6,1fr);gap:7px}
.partner{height:73px;border:1px solid var(--line);display:flex;align-items:center;justify-content:center;font-weight:700;font-size:20px;color:#3a3a3a}
.partner.sel{border:2px solid var(--purple)}
.arrow-btn{position:absolute;width:36px;height:36px;border-radius:50%;border:1px solid var(--line);display:flex;align-items:center;justify-content:center}
.arrow-btn svg{width:12px;height:12px}
.rule{position:absolute;left:99px;top:848px;width:1002px;height:1px;background:var(--line)}

/* headings */
.sec-head{position:absolute;left:0;width:1200px;display:flex;justify-content:center;align-items:center;gap:10px}
.sec-head .dot,.about-head .dot{width:36px;height:36px;border-radius:50%;background:var(--purple)}
.sec-head h2,.about-head h2{font-size:33px}
.sec-sub{position:absolute;left:0;top:970px;width:1200px;text-align:center;font-size:14px}

/* services */
.service{position:absolute;top:1086px;width:323px;height:226px;color:var(--white);text-align:center;padding:69px 26px 0;box-shadow:0 14px 12px -10px rgba(0,0,0,.25)}
.service h3{color:var(--white);font-family:"Open Sans",sans-serif;font-weight:600;font-size:18px;margin-bottom:10px}
.service p{font-size:12px;line-height:21px}
.service .more{display:inline-flex;align-items:center;gap:6px;margin-top:12px;font-size:12.5px;text-decoration:underline;font-weight:600}
.service-badge{position:absolute;top:-56px;left:108px;width:106px;height:106px;border-radius:50%;background:var(--white);border:4px solid currentColor;display:flex;align-items:center;justify-content:center}
.service-badge div{width:76px;height:76px;border-radius:50%}
.s1{left:99px;background:var(--orange)}
.s2{left:439px;background:var(--teal)}
.s3{left:777px;background:var(--amber)}

/* about */
.about{position:absolute;left:0;top:1378px;width:1200px;height:536px;background:linear-gradient(135deg,#f6f6f6,#ececec 60%,#f4f4f4)}
.about-head{position:absolute;left:101px;top:98px;display:flex;align-items:center;gap:10px}
.about-text{position:absolute;left:101px;top:166px;width:498px;font-size:12.5px;line-height:24px}
.about-text p{margin-bottom:8px}
.read-btn{position:absolute;left:101px;top:395px;width:150px;height:39px;border-radius:20px;background:var(--purple);color:var(--white);font-weight:700;font-size:14px;display:flex;align-items:center;justify-content:center}
.monitor{position:absolute;left:654px;top:91px}

/* news */
.news{position:absolute;top:2070px;width:324px;height:220px;border:1px solid var(--line);border-top:4px solid;background:var(--white)}
.news .date{position:absolute;left:0;top:0;width:58px;height:68px;color:var(--white);text-align:center;font-family:"Ubuntu",sans-serif;line-height:1.1;padding-top:6px}
.news .date b{display:block;font-size:23px;font-weight:500}
.news .date span{font-size:19px}
.news h4{position:absolute;left:71px;top:16px;width:240px;font-family:"Open Sans",sans-serif;font-weight:400;font-size:17px;line-height:27px;color:var(--ink)}
.news p{position:absolute;left:12px;top:86px;width:300px;font-size:12px;line-height:24px;color:#a3a3a3}
.news .more{position:absolute;left:12px;top:178px;font-size:12.5px}
.n1{left:99px;border-top-color:var(--orange)} .n1 .date{background:var(--orange)} .n1 .more{color:var(--orange)}
.n2{left:439px;border-top-color:var(--teal)} .n2 .date{background:var(--teal)} .n2 .more{color:var(--teal)}
.n3{left:777px;border-top-color:var(--amber)} .n3 .date{background:var(--amber)} .n3 .more{color:var(--amber)}

/* footer */
.site-footer{position:absolute;left:0;top:2367px;width:1200px;height:381px;background:var(--footer);border-top:4px solid var(--orange);color:#e8e8e8}
.site-footer h4{color:var(--white);font-family:"Open Sans",sans-serif;font-weight:600;font-size:16.5px;position:absolute;top:64px}
.f-contact{position:absolute;left:99px;top:110px;font-size:12px;line-height:19px}
.f-contact li{list-style:none;display:flex;gap:18px;margin-bottom:12px}
.f-contact svg{width:13px;height:13px;flex:none;margin-top:3px}
.f-links{position:absolute;left:355px;top:108px;font-size:12px;list-style:none}
.f-links li{margin-bottom:12px}
.f-news{position:absolute;left:527px;top:108px;width:265px;font-size:12px;line-height:21px}
.f-input{margin-top:18px;width:265px;height:36px;background:var(--white);color:#a0a0a0;font-size:12px;padding:10px 14px}
.f-sub{margin-top:18px;width:108px;height:32px;border-radius:16px;background:var(--purple);color:var(--white);font-size:12px;display:flex;align-items:center;justify-content:center}
.f-social{position:absolute;left:845px;top:113px;display:flex;gap:7px}
.f-social span{width:38px;height:38px;border-radius:50%;border:2px solid var(--white)}
.f-rule{position:absolute;left:99px;top:307px;width:1002px;height:1px;background:#444}
.f-copy{position:absolute;left:0;top:336px;width:1200px;text-align:center;font-size:12px}
</style>
</head>
<body>

<header class="site-header">
  <div class="brand">
    <span class="brand-dot"></span>
    <div class="brand-text">
      <span class="brand-name">Zorvan Lumet</span>
      <span class="brand-tagline">your IT, networks and security partner</span>
    </div>
  </div>
  <nav class="main-nav">
    <a class="active" href="#"><svg viewBox="0 0 12 12"><path d="M6 1 0 6h2v5h3V8h2v3h3V6h2z" fill="#fff"/></svg>Home</a>
    <a href="#"><svg viewBox="0 0 12 12"><circle cx="4" cy="7" r="3" fill="none" stroke="#2d2d2d" stroke-width="2"/><circle cx="9.5" cy="3" r="2" fill="none" stroke="#2d2d2d" stroke-width="1.5"/></svg>Services</a>
    <a href="#"><svg viewBox="0 0 12 12"><circle cx="6" cy="3.5" r="3" fill="#2d2d2d"/><path d="M0 12c0-4 3-5 6-5s6 1 6 5z" fill="#2d2d2d"/></svg>About us</a>
    <a href="#"><svg viewBox="0 0 12 12"><path d="M2 0h3l1 3-2 1c1 2 2 3 4 4l1-2 3 1v3c0 1-1 2-2 2C5 12 0 7 0 2 0 1 1 0 2 0z" fill="#2d2d2d"/></svg>Contact us</a>
  </nav>
  <div class="login-btn"><svg width="11" height="12" viewBox="0 0 11 12"><rect x="0" y="5" width="11" height="7" fill="#fff"/><path d="M2.5 5V3.5a3 3 0 0 1 6 0V5" fill="none" stroke="#fff" stroke-width="1.6"/></svg>CUSTOMER LOG IN</div>
</header>

<section class="hero" role="img" aria-label="Photograph of the London skyline with the clock tower, parliament buildings and a river bridge at dusk">
  <h1 class="hero-title">ZORVAN LUMET</h1>
  <div class="hero-sub">Business Continuity <i></i> IT Support &amp; Field Services <i></i> Outsourced Service Desk</div>
  <div class="hero-dots"><span class="on"></span><span></span><span></span><span></span></div>
</section>

<div class="arrow-btn" style="left:62px;top:695px"><svg viewBox="0 0 12 12"><path d="M8 1 3 6l5 5" fill="none" stroke="#bbb" stroke-width="1.6"/></svg></div>
<div class="arrow-btn" style="left:1099px;top:695px"><svg viewBox="0 0 12 12"><path d="M4 1l5 5-5 5" fill="none" stroke="#bbb" stroke-width="1.6"/></svg></div>
<div class="partners">
  <div class="partner sel">Orvale</div>
  <div class="partner">Brentic</div>
  <div class="partner">Talvora</div>
  <div class="partner">Quillmark</div>
  <div class="partner">Vestrane</div>
  <div class="partner">Parlow</div>
  <div class="partner">Morvent</div>
  <div class="partner">Kelmail</div>
  <div class="partner">Dravix</div>
  <div class="partner">Corlane</div>
  <div class="partner">Sentovia</div>
  <div class="partner">Halvern</div>
</div>
<div class="rule"></div>

<div class="sec-head" style="top:910px"><span class="dot"></span><h2>Our Services</h2></div>
<p class="sec-sub">Duis aute irure dolor in reprehenderit in voluptate velit esse cillum dolore eu fugiat nulla pariatur</p>

<article class="service s1">
  <div class="service-badge" style="color:var(--orange)"><div role="img" aria-label="Illustration of a businessman holding a security shield" style="background:radial-gradient(circle at 50% 40%,#e8eef5 0%,#f7d6c8 55%,#f3b9a3 100%)"></div></div>
  <h3>Business Continuity</h3>
  <p>Sed ut perspiciatis unde omnis iste natus error sit voluptatem accusantium doloremque laudantium totam rem aperiam.</p>
  <span class="more">Read More <svg width="12" height="12" viewBox="0 0 12 12"><circle cx="6" cy="6" r="6" fill="#fff"/><path d="M5 3l3 3-3 3" fill="none" stroke="#f0673f" stroke-width="1.5"/></svg></span>
</article>
<article class="service s2">
  <div class="service-badge" style="color:var(--teal)"><div role="img" aria-label="Illustration of a gear surrounded by support tools" style="background:radial-gradient(circle at 50% 50%,#f4fbfc 0%,#c8e9ec 55%,#9fd6db 100%)"></div></div>
  <h3>IT Support &amp; Field Services</h3>
  <p>Sed ut perspiciatis unde omnis iste natus error sit voluptatem accusantium doloremque laudantium totam rem aperiam.</p>
  <span class="more">Read More <svg width="12" height="12" viewBox="0 0 12 12"><circle cx="6" cy="6" r="6" fill="#fff"/><path d="M5 3l3 3-3 3" fill="none" stroke="#36b3bd" stroke-width="1.5"/></svg></span>
</article>
<article class="service s3">
  <div class="service-badge" style="color:var(--amber)"><div role="img" aria-label="Illustration of a service desk operator wearing a headset" style="background:radial-gradient(circle at 50% 50%,#fffaf0 0%,#fbe3bb 55%,#f8cf86 100%)"></div></div>
  <h3>Outsourced Service Desk</h3>
  <p>Sed ut perspiciatis unde omnis iste natus error sit voluptatem accusantium doloremque laudantium totam rem aperiam.</p>
  <span class="more">Read More <svg width="12" height="12" viewBox="0 0 12 12"><circle cx="6" cy="6" r="6" fill="#fff"/><path d="M5 3l3 3-3 3" fill="none" stroke="#f6a21b" stroke-width="1.5"/></svg></span>
</article>

<section class="about">
  <div class="about-head"><span class="dot"></span><h2>About us</h2></div>
  <div class="about-text">
    <p>Sed ut perspiciatis unde omnis iste natus error sit voluptatem accusantium doloremque laudantium, totam rem aperiam, eaque ipsa quae ab illo inventore veritatis et quasi architecto beatae vitae dicta sunt explicabo. Nemo enim ipsam voluptatem quia voluptas sit aspernatur aut odit..</p>
    <p>Nemo enim ipsam voluptatem quia voluptas sit aspernatur aut odit aut fugit, sed quia consequuntur magni dolores eos qui ratione voluptione voluptatem sequi nesciuntque porro quisquam est..</p>
  </div>
  <div class="read-btn">READ MORE</div>
  <svg class="monitor" width="445" height="357" viewBox="0 0 445 357">
    <defs>
      <radialGradient id="screenGlow" cx="0.6" cy="0.45" r="0.75">
        <stop offset="0" stop-color="#4f8fb0"/>
        <stop offset="0.5" stop-color="#24566f"/>
        <stop offset="1" stop-color="#0f2a3a"/>
      </radialGradient>
    </defs>
    <rect x="0" y="0" width="445" height="264" rx="8" fill="#111"/>
    <rect x="18" y="16" width="409" height="222" fill="url(#screenGlow)" role="img" aria-label="Photograph of a hand touching an IT help desk interface with service icons"/>
    <rect x="0" y="264" width="445" height="34" rx="4" fill="#dcdcdc"/>
    <path d="M180 298h85l12 48H168z" fill="#cfcfcf"/>
    <rect x="150" y="344" width="145" height="8" rx="4" fill="#bdbdbd"/>
  </svg>
</section>

<div class="sec-head" style="top:1986px"><span class="dot"></span><h2>News</h2></div>
<div class="arrow-btn" style="left:30px;top:2162px"><svg viewBox="0 0 12 12"><path d="M8 1 3 6l5 5" fill="none" stroke="#bbb" stroke-width="1.6"/></svg></div>
<div class="arrow-btn" style="left:1134px;top:2162px"><svg viewBox="0 0 12 12"><path d="M4 1l5 5-5 5" fill="none" stroke="#bbb" stroke-width="1.6"/></svg></div>

<article class="news n1">
  <div class="date"><b>09</b><span>Jan</span></div>
  <h4>Quis nostercitation ullamco cum soluta nobis</h4>
  <p>At vero eos et accusamus et iusto odio dignissimos ducimus qui blanditiis um voluptatum deleniti atque corrupti quos doloress..</p>
  <span class="more">Read More »</span>
</article>
<article class="news n2">
  <div class="date"><b>09</b><span>Jan</span></div>
  <h4>Et harum quidem rerum facilis edistinctio</h4>
  <p>At vero eos et accusamus et iusto odio dignissimos ducimus qui blanditiis um voluptatum deleniti atque corrupti quos doloress..</p>
  <span class="more">Read More »</span>
</article>
<article class="news n3">
  <div class="date"><b>09</b><span>Jan</span></div>
  <h4>Itaque earum rerum hic tenetu delectus</h4>
  <p>At vero eos et accusamus et iusto odio dignissimos ducimus qui blanditiis um voluptatum deleniti atque corrupti quos doloress..</p>
  <span class="more">Read More »</span>
</article>

<footer class="site-footer">
  <h4 style="left:99px">Contact Us</h4>
  <h4 style="left:355px">Quick Links</h4>
  <h4 style="left:527px">Newsletter Subscription</h4>
  <h4 style="left:845px">Social Media</h4>
  <ul class="f-contact">
    <li><svg viewBox="0 0 12 12"><path d="M6 0a4 4 0 0 1 4 4c0 3-4 8-4 8S2 7 2 4a4 4 0 0 1 4-4z" fill="#fff"/><circle cx="6" cy="4" r="1.5" fill="#1f1f1f"/></svg><span>27, quasi archbeatae vitae<br>dicta sunt explicabo</span></li>
    <li><svg viewBox="0 0 12 12"><path d="M2 0h3l1 3-2 1c1 2 2 3 4 4l1-2 3 1v3c0 1-1 2-2 2C5 12 0 7 0 2 0 1 1 0 2 0z" fill="#fff"/></svg><span>1 888 888 8888</span></li>
    <li><svg viewBox="0 0 12 12"><rect x="0" y="3" width="12" height="9" fill="#fff"/><rect x="3" y="0" width="6" height="4" fill="#fff"/></svg><span>1 888 888 8888</span></li>
    <li><svg viewBox="0 0 12 12"><rect x="0" y="2" width="12" height="8" fill="#fff"/><path d="M0 2l6 5 6-5" fill="none" stroke="#1f1f1f"/></svg><span>info@companyname.com</span></li>
  </ul>
  <ul class="f-links"><li>Home</li><li>About us</li><li>Services</li><li>Contact us</li></ul>
  <div class="f-news">Register your Email Address to get Information about us
    <div class="f-input">Email Address</div>
    <div class="f-sub">SUBSCRIBE</div>
  </div>
  <div class="f-social" role="list" aria-label="Social media links">
    <span role="listitem" aria-label="Social network link 1"></span>
    <span role="listitem" aria-label="Social network link 2"></span>
    <span role="listitem" aria-label="Social network link 3"></span>
    <span role="listitem" aria-label="Social network link 4"></span>
    <span role="listitem" aria-label="Social network link 5"></span>
  </div>
  <div class="f-rule"></div>
  <p class="f-copy">Copyrights © 2018, Zorvan Lumet.All rights reserved. &nbsp;| &nbsp;Privacy policy</p>
</footer>

</body>
</html>
```